BOLD & MINIMALIST DESIGN NEEDED

We want a very bold but minimalistic business card design that is impactful and utilizes both sides of the business card. Our current logo is included for your use.

We want bold fonts and good use of negative space. We don't want the logo to overpower the design.

Target Market(s)

Professionals who are building new commercial buildings.

Industry/Entity Type

Construction

Contact Information for Business Card

Name, Title, email, office phone, cell phone, website

Font styles to use
Serif
Sans Serif

Requirements
Must have
• Bold design!

```html
<!DOCTYPE html>
<html lang="en">
<head>
<meta charset="utf-8">
<title>Ridgeline Design + Build — Business Card</title>
<link rel="stylesheet" href="https://fonts.googleapis.com/css2?family=Montserrat:wght@400;500;800;900&display=swap">
<style>
  :root {
    --backdrop: #3a3a3a;
    --lime: #86c440;
    --lime-light: #9fd25e;
    --lime-deep: #4d8a2a;
    --ink: #111111;
    --paper: #ffffff;
  }
  * { box-sizing: border-box; margin: 0; padding: 0; }
  html, body {
    width: 1200px; height: 689px; overflow: hidden;
    background: var(--backdrop);
    font-family: "Montserrat", sans-serif;
  }
  .canvas { position: relative; width: 1200px; height: 689px; }
  .card {
    position: absolute; top: 190px;
    width: 540px; height: 309px;
    border-radius: 22px; overflow: hidden;
  }
  .card--front {
    left: 40px;
    background: linear-gradient(115deg, var(--lime-light) 0%, var(--lime) 45%, var(--lime) 100%);
  }
  .card--back { left: 620px; background: var(--lime); }

  .front-name {
    position: absolute; left: 0; right: 0; top: 96px;
    display: flex; align-items: center; justify-content: center; gap: 14px;
    color: var(--lime-deep);
  }
  .front-name .mark-square { width: 34px; height: 34px; background: var(--lime-deep); }
  .front-name .brand {
    font-weight: 900; font-size: 44px; line-height: 1; letter-spacing: 1px;
  }
  .front-name .brand small {
    display: block; font-size: 44px; font-weight: 900;
  }

  .back-shape { position: absolute; inset: 0; }

  .back-brand {
    position: absolute; right: 30px; top: 108px;
    width: 172px;
    color: var(--ink);
    font-weight: 900;
    text-align: center;
  }
  .back-brand .brand-name {
    display: block; font-size: 27px; line-height: 1; letter-spacing: 0.5px;
  }
  .back-brand .brand-line {
    display: block; font-size: 12px; line-height: 1;
    letter-spacing: 3.2px; margin-top: 8px;
    padding-top: 6px; border-top: 1.5px solid var(--ink);
  }

  .contact {
    position: absolute; left: 30px; top: 48px;
    color: var(--paper);
  }
  .contact .person { font-weight: 800; font-size: 26px; letter-spacing: 1px; }
  .contact .role { font-weight: 400; font-size: 13px; letter-spacing: 0.5px; margin-top: 2px; }
  .contact .address { font-size: 13px; line-height: 1.45; margin-top: 22px; margin-left: 30px; }
  .contact .lines { list-style: none; margin-top: 22px; margin-left: 30px; }
  .contact .lines li {
    display: flex; align-items: center; gap: 8px;
    font-size: 13px; line-height: 1.7;
  }
  .contact .lines svg { width: 12px; height: 12px; flex: none; }
</style>
</head>
<body>
<main class="canvas">

  <section class="card card--front" aria-label="Card front">
    <div class="front-name">
      <span class="mark-square"></span>
      <p class="brand">RIDGELINE<small>DESIGN + BUILD</small></p>
    </div>
  </section>

  <section class="card card--back" aria-label="Card back">
    <svg class="back-shape" viewBox="0 0 540 309" preserveAspectRatio="none" aria-hidden="true">
      <path d="M280,0 L540,0 L540,309 L470,309 C370,300 335,255 322,150 C314,80 302,30 280,0 Z" fill="var(--paper)"/>
      <path d="M276,0 C300,30 312,80 318,150 C330,255 368,300 470,309 L455,309 C355,298 318,250 308,150 C302,80 292,30 270,0 Z" fill="var(--ink)"/>
      <path d="M330,140 C338,230 370,285 440,296 C380,292 340,250 330,140 Z" fill="var(--lime)"/>
    </svg>

    <p class="back-brand">
      <span class="brand-name">RIDGELINE</span>
      <span class="brand-line">DESIGN + BUILD</span>
    </p>

    <div class="contact">
      <h1 class="person">MARCUS HALE</h1>
      <p class="role">OWNER-CEO</p>
      <p class="address">Your address,<br>City State, Zip 1234</p>
      <ul class="lines">
        <li>
          <svg viewBox="0 0 12 12"><path d="M2 1h3l1 3-2 1a6 6 0 0 0 3 3l1-2 3 1v3c-6 0-10-4-10-9z" fill="var(--paper)"/></svg>
          123 456 789
        </li>
        <li>
          <svg viewBox="0 0 12 12"><rect x="3" y="0.5" width="6" height="11" rx="1" fill="none" stroke="var(--paper)"/></svg>
          123 456 789
        </li>
        <li>
          <svg viewBox="0 0 12 12"><rect x="0.5" y="2.5" width="11" height="7" fill="var(--paper)"/><path d="M0.5 2.5l5.5 4 5.5-4" fill="none" stroke="var(--lime)"/></svg>
          info@ridgelinebuild.com
        </li>
        <li>
          <svg viewBox="0 0 12 12"><circle cx="6" cy="6" r="5.5" fill="var(--paper)"/><path d="M0.5 6h11M6 0.5c-3 3-3 8 0 11M6 0.5c3 3 3 8 0 11" fill="none" stroke="var(--lime)" stroke-width="0.8"/></svg>
          www.ridgelinebuild.com
        </li>
      </ul>
    </div>
  </section>

</main>
</body>
</html>
```